product development company BRVEMKO LLC business card

We need a business card design for a company based in Texas called 'BRVEMKO LLC'. Our first product is a illuminated portable ice chest that is called ' Copper Harbor coolers'. Copper harbor coolers is trademarked. I would like to have the copper harbor trademark somewhere on the card as well as the BRVEMKO LLC name.

Target Market(s)

outdoor industry

Industry/Entity Type

Business

Contact Information for Business Card

i would like to have BRVEMKO LLC logo larger than the Copper harbor coolers logo.

Font styles to use
Serif
Sans Serif

```html
<!DOCTYPE html>
<html lang="en">
<head>
<meta charset="utf-8">
<title>BRVEMKO LLC – Business Card</title>
<link rel="stylesheet" href="https://fonts.googleapis.com/css2?family=Marcellus&family=Tinos:wght@400;700&family=Montserrat:wght@800&display=swap">
<style>
  :root {
    --page-bg: #e6e4e1;
    --card-bg: #ffffff;
    --ink: #0b0b0b;
    --muted: #9a9a9a;
    --swoosh: #a8a8a8;
    --divider: #b5b5b5;
  }
  html, body {
    margin: 0;
    padding: 0;
    width: 1200px;
    height: 902px;
    overflow: hidden;
    background: var(--page-bg);
  }
  .card {
    position: absolute;
    left: 100px;
    top: 165px;
    width: 1000px;
    height: 571px;
    background: var(--card-bg);
    border-radius: 24px;
    overflow: hidden;
    box-shadow: 0 6px 24px rgba(0,0,0,0.12);
  }
  .card__wave {
    position: absolute;
    left: 0;
    top: 0;
    width: 1000px;
    height: 571px;
  }
  .brand {
    position: absolute;
    left: 46px;
    top: 200px;
    width: 408px;
    text-align: center;
    color: var(--ink);
  }
  .brand__name {
    font-family: "Marcellus", serif;
    font-size: 58px;
    letter-spacing: 5px;
    line-height: 1;
    margin: 0;
  }
  .brand__suffix {
    display: flex;
    align-items: center;
    justify-content: center;
    gap: 14px;
    margin-top: 10px;
    font-family: "Marcellus", serif;
    font-size: 30px;
    letter-spacing: 12px;
    line-height: 1;
  }
  .brand__dots {
    width: 66px;
    border-top: 3px dotted var(--ink);
  }
  .divider {
    position: absolute;
    left: 493px;
    top: 99px;
    width: 2px;
    height: 313px;
    background: var(--divider);
  }
  .person {
    position: absolute;
    left: 537px;
    top: 100px;
    font-family: "Tinos", serif;
  }
  .person__name {
    margin: 0;
    font-size: 40px;
    font-weight: 400;
    color: var(--ink);
    line-height: 1;
  }
  .person__title {
    margin: 2px 0 0;
    font-size: 28px;
    font-weight: 700;
    color: var(--muted);
    line-height: 1;
  }
  .contact {
    position: absolute;
    left: 537px;
    top: 228px;
    font-family: "Tinos", serif;
    font-size: 27px;
    color: var(--muted);
    line-height: 1;
  }
  .contact__row {
    display: flex;
    align-items: center;
    gap: 8px;
    height: 37px;
  }
  .contact__icon {
    width: 30px;
    height: 30px;
    flex: none;
  }
  .contact__web {
    margin-top: 6px;
    font-size: 26px;
  }
  .product {
    position: absolute;
    left: 537px;
    top: 380px;
    display: flex;
    align-items: center;
    gap: 10px;
    font-family: "Montserrat", sans-serif;
    font-weight: 800;
    font-size: 24px;
    color: var(--ink);
  }
  .product__mark {
    width: 22px;
    height: 22px;
    background: var(--ink);
  }
</style>
</head>
<body>
  <div class="card">
    <svg class="card__wave" viewBox="0 0 1000 571" aria-hidden="true">
      <path fill="var(--swoosh)" d="M0 440 C 240 505 450 520 620 492 C 780 466 880 430 1000 426 L1000 571 L0 571 Z"/>
      <path fill="#ffffff" d="M0 446 C 240 516 450 532 620 505 C 780 480 880 444 1000 440 L1000 571 L0 571 Z"/>
      <path fill="var(--ink)" d="M0 452 C 240 528 450 545 620 518 C 780 494 880 456 1000 450 L1000 571 L0 571 Z"/>
    </svg>

    <div class="brand">
      <h1 class="brand__name">BRVEMKO</h1>
      <div class="brand__suffix">
        <span class="brand__dots"></span><span>LLC</span><span class="brand__dots"></span>
      </div>
    </div>

    <div class="divider"></div>

    <div class="person">
      <h2 class="person__name">EMPLOYEE NAME</h2>
      <p class="person__title">Maneger</p>
    </div>

    <div class="contact">
      <div class="contact__row">
        <svg class="contact__icon" viewBox="0 0 30 30" aria-hidden="true">
          <rect width="30" height="30" rx="4" fill="var(--ink)"/>
          <path fill="#fff" d="M10 6 l4 0 l1 5 l-3 2 c1 3 3 5 6 6 l2 -3 l5 1 l0 4 c0 2 -2 3 -4 3 c-8 -1 -14 -7 -15 -15 c0 -2 1 -3 4 -3 z"/>
        </svg>
        <span>123 456 7890</span>
      </div>
      <div class="contact__row">
        <svg class="contact__icon" viewBox="0 0 30 30" aria-hidden="true">
          <rect width="30" height="30" rx="4" fill="var(--ink)"/>
          <rect x="5" y="8" width="20" height="14" fill="none" stroke="#fff" stroke-width="2"/>
          <path d="M5 8 L15 16 L25 8" fill="none" stroke="#fff" stroke-width="2"/>
        </svg>
        <span>your@yourcompany.com</span>
      </div>
      <div class="contact__web">www.yourcompany.com</div>
    </div>

    <div class="product">
      <span class="product__mark"></span>
      <span>Copper Harbor</span>
    </div>
  </div>
</body>
</html>
```